Vantor Ridge needs a Business Card Design

We need a business card design for an Information Technology company based in Fairfax Virginia called Vantor Ridge. We want the business card to use our logo colors. We need it to be double-sided. The business card needs to look professional but we would like it to be unique. You can get company information from our web site (http://www.vantorridgellc.example).

Target Market(s)

Target market is Government Agencies and Business Professionals.

Industry/Entity Type

Business

Requirements
Must have
• Must have section for company name, company address, company URL, employee name, title, phone and email. Also must have company logo and space for entering logos.

```html
<!DOCTYPE html>
<html lang="en">
<head>
<meta charset="utf-8">
<title>Vantor Ridge – Business Card</title>
<link rel="stylesheet" href="https://fonts.googleapis.com/css2?family=Open+Sans:wght@400;600;700&display=swap">
<style>
  :root {
    --stage: #eceef2;
    --paper: #ffffff;
    --navy: #1f2b8f;
    --navy-deep: #18207a;
    --royal: #2a3aa8;
    --sky: #1b7fc4;
    --ink-light: #ffffff;
    --ink-soft: #cdd6f5;
  }
  * { box-sizing: border-box; margin: 0; padding: 0; }
  html, body { width: 1200px; height: 1024px; overflow: hidden; }
  body {
    background: var(--stage);
    font-family: "Open Sans", Arial, sans-serif;
    display: flex;
    flex-direction: column;
    align-items: center;
    justify-content: center;
    gap: 56px;
  }
  .card {
    width: 700px;
    height: 400px;
    position: relative;
    overflow: hidden;
    box-shadow: 0 6px 18px rgba(20, 30, 80, 0.18);
  }

  /* Front */
  .card-front { background: var(--paper); }
  .front-brand {
    position: absolute;
    top: 0; left: 0; right: 0;
    height: 226px;
    display: flex;
    align-items: center;
    justify-content: center;
    gap: 18px;
  }
  .brand-square {
    width: 44px; height: 44px;
    background: var(--navy);
  }
  .brand-name {
    font-weight: 700;
    font-size: 48px;
    color: var(--navy);
    letter-spacing: 0.5px;
    text-transform: uppercase;
  }
  .front-rule {
    position: absolute;
    left: 0; right: 0;
    top: 228px;
    height: 5px;
    background: var(--sky);
  }
  .front-band {
    position: absolute;
    left: 0; right: 0;
    top: 241px; bottom: 0;
    background: linear-gradient(180deg, var(--royal), var(--navy-deep));
    color: var(--ink-light);
    display: flex;
    justify-content: space-between;
    padding: 26px 40px 26px 40px;
  }
  .identity { align-self: flex-end; }
  .person-name { font-weight: 700; font-size: 19px; }
  .person-title { font-size: 15px; color: var(--ink-soft); margin-bottom: 6px; }
  .address { display: flex; gap: 8px; font-size: 16px; line-height: 1.3; }
  .divider { align-self: center; }
  .contacts { list-style: none; font-size: 15px; line-height: 1.55; align-self: flex-start; }
  .contacts li { display: flex; align-items: center; gap: 8px; }
  .icon { width: 13px; height: 13px; flex: none; fill: var(--sky); }
  .address .icon { margin-top: 4px; }

  /* Back */
  .card-back {
    background: linear-gradient(160deg, var(--royal) 0%, var(--navy) 60%, var(--navy-deep) 100%);
  }
  .back-url {
    position: absolute;
    top: 26px; left: 34px;
    font-size: 12px;
    font-style: italic;
    color: var(--ink-soft);
  }
  .back-brand {
    position: absolute;
    left: 60px; bottom: 60px;
    display: flex;
    align-items: center;
    gap: 14px;
  }
  .back-brand .brand-square { width: 34px; height: 34px; background: var(--ink-light); }
  .back-brand .brand-name { color: var(--ink-light); font-size: 36px; }
</style>
</head>
<body>

  <section class="card card-front" aria-label="Business card front">
    <div class="front-brand">
      <span class="brand-square"></span>
      <span class="brand-name">Vantor Ridge</span>
    </div>
    <div class="front-rule"></div>
    <div class="front-band">
      <div class="identity">
        <p class="person-name">Daniel Marsh</p>
        <p class="person-title">Job Title</p>
        <div class="address">
          <svg class="icon" viewBox="0 0 12 12"><path d="M6 0 12 6H10V12H7V8H5V12H2V6H0Z"/></svg>
          <p>4410 Linden Court, Suite 120<br>Fairfax, VA 22030</p>
        </div>
      </div>
      <svg class="divider" width="70" height="30" viewBox="0 0 70 30"><line x1="0" y1="28" x2="70" y2="2" stroke="rgba(255,255,255,0.45)" stroke-width="1.5"/></svg>
      <ul class="contacts">
        <li><svg class="icon" viewBox="0 0 12 12"><path d="M2 0h3l1 3-2 1.5a7 7 0 0 0 3.5 3.5L9 6l3 1v3a2 2 0 0 1-2 2A10 10 0 0 1 0 2a2 2 0 0 1 2-2z"/></svg>877.555.0142</li>
        <li><svg class="icon" viewBox="0 0 12 12"><rect x="3" y="0" width="6" height="12" rx="1.5"/></svg>888.555.0187</li>
        <li><svg class="icon" viewBox="0 0 12 12"><path d="M0 2h12v8H0z M0 2l6 4 6-4" stroke="#1f2b8f" stroke-width="0.8"/></svg>name@vantorridge.example</li>
        <li><svg class="icon" viewBox="0 0 12 12"><circle cx="6" cy="6" r="5.5"/></svg>www.vantorridgellc.example</li>
      </ul>
    </div>
  </section>

  <section class="card card-back" aria-label="Business card back">
    <p class="back-url">www.vantorridgellc.example</p>
    <div class="back-brand">
      <span class="brand-square"></span>
      <span class="brand-name">Vantor Ridge</span>
    </div>
  </section>

</body>
</html>
```